Ridgeline Haul Carriers - Website

A clean, not cluttered informative website for our business. We specialize in the transportation of radioactive materials across North America. The site is mostly for information about our company and will not be used to attract business but will be used to attract employee's mainly drivers. Driver's are very hard to find in our area. One of the pages needs to be a job's posting page with an apply now button. Either an application can be filled out there or a resume can be uploaded which ever functionality works better. I would like a website that I can easily edit, ability to change text and photos.

Number of Pages Required

5+ page

Colors

Designer to choose colors to be used in the design.

Requirements
Must have
• Home - About - Services - Jobs - Contact pages
• A way prospective employee's can apply or upload their resume to be emailed to me
• Very clean apperance
Should not have
• I don't want it to be busy

```html
<!DOCTYPE html>
<html lang="en">
<head>
<meta charset="utf-8">
<title>Ridgeline Haul Carriers</title>
<link href="https://fonts.googleapis.com/css2?family=Jost:wght@400;500;600&family=Michroma&family=Orbitron:wght@700;800&display=swap" rel="stylesheet">
<style>
:root{
  --blue:#1769b8;
  --ink:#222;
  --text:#444;
  --grey:#9a9a9a;
  --btn:#9b9b9b;
  --footer:#262626;
  --footer-bar:#3d3d3d;
  --white:#fff;
}
*{box-sizing:border-box;margin:0;padding:0}
html,body{width:1200px;height:2894px;overflow:hidden}
body{position:relative;background:var(--white);font-family:'Jost',sans-serif;color:var(--text)}
.abs{position:absolute}
/* header */
.site-header{left:0;top:0;width:1200px;height:105px;background:var(--white)}
.brand{left:145px;top:30px;display:flex;align-items:center;gap:10px;font-weight:600;font-size:27px;color:var(--blue);letter-spacing:.5px}
.brand-dot{width:16px;height:16px;border-radius:50%;background:var(--blue)}
.top-phone{right:146px;top:18px;font-family:'Michroma',sans-serif;font-size:15px;color:var(--grey);display:flex;align-items:center;gap:10px}
.main-nav{left:487px;top:63px;display:flex;font-family:'Michroma',sans-serif;font-size:13px;color:var(--grey)}
.main-nav a{color:inherit;text-decoration:none;margin-right:50px;padding-bottom:6px}
.main-nav a.active{color:var(--blue);border-bottom:3px solid var(--blue)}
.main-nav a:last-child{margin-right:0}
/* hero */
.hero{left:0;top:105px;width:1200px;height:572px;background:linear-gradient(100deg,#3b3d42 0%,#6a5a55 30%,#8e4b44 48%,#b7a99a 62%,#7b8a6a 80%,#55654a 100%);overflow:hidden}
.hero-copy{right:145px;top:265px;text-align:right;color:var(--white)}
.hero-brand{font-size:30px;font-weight:600;margin-bottom:12px;text-shadow:0 1px 4px rgba(0,0,0,.45)}
.hero-line{font-size:29px;font-weight:500;line-height:42px;text-shadow:0 1px 4px rgba(0,0,0,.45)}
.btn{display:inline-flex;align-items:center;border-radius:20px;font-size:15px;color:var(--white);text-decoration:none;height:36px;padding-left:20px}
.btn .arrow{width:36px;height:36px;border-radius:50%;display:flex;align-items:center;justify-content:center;margin-left:14px}
.btn-blue{background:var(--blue)}
.btn-blue .arrow{background:#111}
.btn-grey{background:var(--btn)}
.btn-grey .arrow{background:var(--white);border:2px solid var(--btn)}
.hero .btn{margin-top:20px}
.slider-dots{left:572px;top:513px;display:flex;gap:8px}
.slider-dots span{width:10px;height:10px;border-radius:50%;background:var(--white)}
.slider-dots span.on{background:#e26a1c}
/* sections */
.section-title{width:1200px;left:0;text-align:center;font-family:'Orbitron',sans-serif;font-weight:800;letter-spacing:2px}
.rule{left:490px;width:220px;height:2px;background:#555}
.about-title{top:772px;font-size:30px;color:var(--blue)}
.about-title span{color:var(--grey)}
.about-lead{left:170px;width:860px;top:858px;text-align:center;font-size:16px;line-height:25px;color:var(--ink);font-weight:500}
.about-body{left:170px;width:860px;top:922px;text-align:center;font-size:12.5px;line-height:21px}
.services-band{left:0;top:1121px;width:1200px;height:1152px;background:linear-gradient(180deg,#e4e4e4 0%,#d9d9d9 35%,#c8ccd1 55%,#9aa2ad 80%,#5d6674 100%)}
.light-title{top:1190px;font-size:30px;color:var(--white);text-shadow:0 2px 3px rgba(0,0,0,.4)}
.card{left:143px;width:917px;height:366px;background:var(--white);border-radius:6px;box-shadow:0 10px 24px rgba(0,0,0,.25);overflow:hidden}
.card-photo{position:absolute;top:0;width:462px;height:366px}
.card-body{position:absolute;top:0;width:455px;padding:32px 36px}
.card h3{font-weight:500;font-size:19px;color:var(--blue);margin-bottom:16px}
.card p{font-size:12.5px;line-height:21px;margin-bottom:14px}
.checks{list-style:none;font-size:12.5px;line-height:20px;margin-bottom:16px}
.checks li{display:flex;align-items:center;gap:9px}
.checks svg{flex:none}
.card .btn{font-size:13px;height:34px;padding-left:16px}
.card .btn .arrow{width:34px;height:34px}
.card strong{font-weight:500;color:var(--ink)}
/* cta */
.cta-head{left:0;width:1200px;top:2330px;text-align:center;font-family:'Orbitron',sans-serif;font-weight:800;font-size:27px;line-height:46px;letter-spacing:3px;color:#1d1d1d}
/* footer */
.site-footer{left:0;top:2570px;width:1200px;height:288px;background:var(--footer);color:#d8d8d8}
.footer-bar{left:0;top:2858px;width:1200px;height:36px;background:var(--footer-bar);color:#cfcfcf;font-size:12px;text-align:center;line-height:36px}
.f-col{top:52px}
.f-col h4{font-family:'Michroma',sans-serif;font-size:12px;font-weight:400;letter-spacing:1.5px;color:#cfcfcf;margin-bottom:8px}
.f-col h4::after{content:"";display:block;width:44px;height:1px;background:#777;margin-top:10px}
.f-col ul{list-style:none;font-size:12px;line-height:28px;margin-top:14px}
.f-col ul li::before{content:"•";margin-right:10px}
.f-row{display:flex;gap:14px;font-size:12px;line-height:18px;margin-top:20px;align-items:flex-start}
.f-sep{top:40px;width:1px;height:180px;background:#444}
.map{width:200px;height:124px;border-radius:4px;background:linear-gradient(135deg,#e9e4d6,#cfe0c4 50%,#d9e4ee);margin-top:18px}
.social{display:flex;align-items:center;gap:12px;font-size:12px;margin-top:16px}
.social span.circle{width:34px;height:34px;border-radius:50%;background:#3a3a3a;display:block}
</style>
</head>
<body>

<header class="abs site-header">
  <div class="abs brand"><span class="brand-dot"></span>Ridgeline Haul Carriers</div>
  <div class="abs top-phone">
    <svg width="16" height="16" viewBox="0 0 24 24"><path fill="#1769b8" d="M6.6 10.8a15 15 0 0 0 6.6 6.6l2.2-2.2c.3-.3.7-.4 1-.2 1.1.4 2.3.6 3.6.6.6 0 1 .4 1 1V20c0 .6-.4 1-1 1A17 17 0 0 1 3 4c0-.6.4-1 1-1h3.5c.6 0 1 .4 1 1 0 1.3.2 2.5.6 3.6.1.3 0 .7-.2 1z"/></svg>
    555-014-2290
  </div>
  <nav class="abs main-nav">
    <a class="active" href="#">HOME</a><a href="#">ABOUT</a><a href="#">SERVICES</a><a href="#">JOBS</a><a href="#">CONTACT</a>
  </nav>
</header>

<section class="abs hero" role="img" aria-label="Close-up of a red transport truck hauling a tanker on a highway">
  <div class="abs hero-copy">
    <div class="hero-brand">Ridgeline Haul Carriers</div>
    <div class="hero-line">Specializing in the Transportation</div>
    <div class="hero-line">of Radioactive Materials</div>
    <div class="hero-line">Across North America</div>
    <a class="btn btn-blue" href="#">Contact Us Today<span class="arrow"><svg width="14" height="12" viewBox="0 0 14 12"><path d="M1 1l5 5-5 5M7 1l5 5-5 5" stroke="#fff" stroke-width="2" fill="none"/></svg></span></a>
  </div>
  <div class="abs slider-dots"><span></span><span class="on"></span><span></span></div>
</section>

<section>
  <h2 class="abs section-title about-title">ABOUT RIDGELINE <span>HAUL CARRIERS</span></h2>
  <div class="abs rule" style="top:823px"></div>
  <p class="abs about-lead">Lorem ipsum dolor sit amet, consectetuer adipiscing elit, sed diam nonummy nibh euismod tincidunt ut laoreet dolore magna aliquam erat volutpat. Ut wisi enim ad minim veniam, quis nostrud exerci tation</p>
  <p class="abs about-body">suscipit lobortis nisl ut aliquip ex ea commodo consequat. Duis autem vel eum iriure dolor in hendrerit in vulputate velit esse molestie consequat, vel illum dolore eu feugiat nulla facilisis at vero eros et accumsan et iusto odio dignissim qui blandit praesent luptatum zzril delenit augue duis dolore te feugait nulla facilisi. elit, sed diam nonummy nibh euismod tincidunt ut laoreet dolore magna aliquam erat volutpat. Ut wisi enim ad minim veniam,</p>
  <a class="abs btn btn-grey" href="#" style="left:538px;top:1005px;font-size:13px">Read More<span class="arrow"><svg width="12" height="10" viewBox="0 0 14 12"><path d="M1 1l5 5-5 5M7 1l5 5-5 5" stroke="#9b9b9b" stroke-width="2" fill="none"/></svg></span></a>
</section>

<div class="abs services-band" role="img" aria-label="Soft blurred view of white trucks parked in a row"></div>

<section>
  <h2 class="abs section-title light-title">SERVICE WE PROVIDE</h2>
  <div class="abs rule" style="top:1243px;background:#666"></div>
  <article class="abs card" style="top:1272px">
    <div class="card-photo" style="left:0;background:linear-gradient(180deg,#7d98b8 0%,#a9bccf 45%,#8e8a7c 62%,#6f6657 100%)" role="img" aria-label="Flatbed truck carrying sealed containers behind a wire fence"></div>
    <div class="card-body" style="left:462px">
      <h3>Transportation of Radioactive Materials</h3>
      <p>Lorem ipsum dolor sit amet, consectetuer adipiscing elit, sed diam no nummy nibh euismod tincidunt ut laoreet dolore magna</p>
      <p>Lorem ipsum dolor sit amet, consectetuer adipiscing elit, sed diamnomy nibh euismod tincidunt ut laoreet dolore magna suscipit lobortis nisl ut aliquip ex ea commodo consequat.</p>
      <ul class="checks">
        <li><svg width="11" height="11" viewBox="0 0 11 11"><rect x=".5" y=".5" width="10" height="10" fill="none" stroke="#444"/><path d="M2.5 5.5l2 2 4-5" stroke="#444" stroke-width="1.4" fill="none"/></svg>injected humour</li>
        <li><svg width="11" height="11" viewBox="0 0 11 11"><rect x=".5" y=".5" width="10" height="10" fill="none" stroke="#444"/><path d="M2.5 5.5l2 2 4-5" stroke="#444" stroke-width="1.4" fill="none"/></svg>true generator on the Internet</li>
        <li><svg width="11" height="11" viewBox="0 0 11 11"><rect x=".5" y=".5" width="10" height="10" fill="none" stroke="#444"/><path d="M2.5 5.5l2 2 4-5" stroke="#444" stroke-width="1.4" fill="none"/></svg>Lorem Ipsum generators</li>
        <li><svg width="11" height="11" viewBox="0 0 11 11"><rect x=".5" y=".5" width="10" height="10" fill="none" stroke="#444"/><path d="M2.5 5.5l2 2 4-5" stroke="#444" stroke-width="1.4" fill="none"/></svg>Many desktop publishing packages</li>
      </ul>
      <a class="btn btn-grey" href="#">Know More<span class="arrow"><svg width="12" height="10" viewBox="0 0 14 12"><path d="M1 1l5 5-5 5M7 1l5 5-5 5" stroke="#9b9b9b" stroke-width="2" fill="none"/></svg></span></a>
    </div>
  </article>

  <h2 class="abs section-title light-title" style="top:1713px">JOIN OUR TEAM</h2>
  <div class="abs rule" style="top:1766px;background:#eee"></div>
  <article class="abs card" style="top:1795px">
    <div class="card-body" style="left:0">
      <h3>Driving Opportunities</h3>
      <p>Lorem ipsum dolor sit amet, consectetuer adipiscing elit, sed diamnomy nibh euismod tincidunt ut laoreet.</p>
      <p><strong>To speak with the Driver Recruiting Department, call 555.014.2290</strong></p>
      <ul class="checks">
        <li><svg width="11" height="11" viewBox="0 0 11 11"><rect x=".5" y=".5" width="10" height="10" fill="none" stroke="#444"/><path d="M2.5 5.5l2 2 4-5" stroke="#444" stroke-width="1.4" fill="none"/></svg>Drivers Apply Online</li>
        <li><svg width="11" height="11" viewBox="0 0 11 11"><rect x=".5" y=".5" width="10" height="10" fill="none" stroke="#444"/><path d="M2.5 5.5l2 2 4-5" stroke="#444" stroke-width="1.4" fill="none"/></svg>Drivers Benefits</li>
        <li><svg width="11" height="11" viewBox="0 0 11 11"><rect x=".5" y=".5" width="10" height="10" fill="none" stroke="#444"/><path d="M2.5 5.5l2 2 4-5" stroke="#444" stroke-width="1.4" fill="none"/></svg>Driving Career Path</li>
        <li><svg width="11" height="11" viewBox="0 0 11 11"><rect x=".5" y=".5" width="10" height="10" fill="none" stroke="#444"/><path d="M2.5 5.5l2 2 4-5" stroke="#444" stroke-width="1.4" fill="none"/></svg>Drivers Frequently Asked Questions</li>
        <li><svg width="11" height="11" viewBox="0 0 11 11"><rect x=".5" y=".5" width="10" height="10" fill="none" stroke="#444"/><path d="M2.5 5.5l2 2 4-5" stroke="#444" stroke-width="1.4" fill="none"/></svg>Drivers Incentive Programs</li>
        <li><svg width="11" height="11" viewBox="0 0 11 11"><rect x=".5" y=".5" width="10" height="10" fill="none" stroke="#444"/><path d="M2.5 5.5l2 2 4-5" stroke="#444" stroke-width="1.4" fill="none"/></svg>Paid Apprenticeship CDL Training</li>
      </ul>
      <a class="btn btn-grey" href="#">Apply Now<span class="arrow"><svg width="12" height="10" viewBox="0 0 14 12"><path d="M1 1l5 5-5 5M7 1l5 5-5 5" stroke="#9b9b9b" stroke-width="2" fill="none"/></svg></span></a>
    </div>
    <div class="card-photo" style="left:455px;background:linear-gradient(180deg,#6f9fd6 0%,#a8c6e6 40%,#e2e6ea 60%,#b9bec4 100%)" role="img" aria-label="Truck driver in the cab of a white truck"></div>
  </article>
</section>

<section>
  <h2 class="abs cta-head">LOREM IPSUM DOLOR SIT AMET CIDUNT UT<br>MAGNA ALIQUAM ERAT VOLUTPAT</h2>
  <a class="abs btn btn-grey" href="#" style="left:512px;top:2460px">Contact Us Today<span class="arrow"><svg width="12" height="10" viewBox="0 0 14 12"><path d="M1 1l5 5-5 5M7 1l5 5-5 5" stroke="#9b9b9b" stroke-width="2" fill="none"/></svg></span></a>
</section>

<footer class="abs site-footer">
  <div class="abs f-col" style="left:145px">
    <h4>QUICK LINKS</h4>
    <ul><li>Home</li><li>About</li><li>Services</li><li>Jobs</li><li>Contact</li></ul>
  </div>
  <div class="abs f-sep" style="left:306px"></div>
  <div class="abs f-col" style="left:357px">
    <h4>CONTACT DETAILS</h4>
    <div class="f-row"><svg width="12" height="14" viewBox="0 0 12 16"><path fill="#ddd" d="M6 0a6 6 0 0 0-6 6c0 4.5 6 10 6 10s6-5.5 6-10a6 6 0 0 0-6-6zm0 8.5A2.5 2.5 0 1 1 6 3.5a2.5 2.5 0 0 1 0 5z"/></svg><span>4410 Cedar Ridge Road<br>Marlowe Falls, North America</span></div>
    <div class="f-row"><svg width="12" height="12" viewBox="0 0 24 24"><path fill="#ddd" d="M6.6 10.8a15 15 0 0 0 6.6 6.6l2.2-2.2c.3-.3.7-.4 1-.2 1.1.4 2.3.6 3.6.6.6 0 1 .4 1 1V20c0 .6-.4 1-1 1A17 17 0 0 1 3 4c0-.6.4-1 1-1h3.5c.6 0 1 .4 1 1 0 1.3.2 2.5.6 3.6.1.3 0 .7-.2 1z"/></svg><span>555-014-2290</span></div>
    <div class="f-row"><svg width="12" height="10" viewBox="0 0 12 10"><rect width="12" height="10" rx="1" fill="#ddd"/><path d="M0 1l6 4 6-4" stroke="#262626" fill="none"/></svg><span>info@ridgelinehaul.com</span></div>
  </div>
  <div class="abs f-sep" style="left:590px"></div>
  <div class="abs f-col" style="left:648px">
    <h4>LOCATION MAP</h4>
    <div class="map" role="img" aria-label="Street map showing the office location"></div>
  </div>
  <div class="abs f-sep" style="left:896px"></div>
  <div class="abs f-col" style="left:948px">
    <h4>FOLLOW US</h4>
    <div class="social"><span class="circle"></span>FRIENDBOOK</div>
    <div class="social"><span class="circle"></span>CHIRPER</div>
    <div class="social"><span class="circle"></span>PROLINK</div>
  </div>
</footer>
<div class="abs footer-bar">Copyright © 2019 Ridgeline Haul Carriers. All Rights Reserved.</div>

</body>
</html>
```